Business Card & Email Signature Design || Upmarket + Luxury

Rima Vale Honey, a New Zealand Manuka Honey company needs a Business Card & Email Signature design.

Our logo's are attached in Gold & Black versions, feel free to be creative with how you use the logo and it's patterns in your design.

Style:
- Looking for an Elegant, Luxurious, Upmarket feel.
- Black/Matte Black Card, Gold Foil, UV Embossing

Information to Add:

- Logo
- Company Name: Rima Vale Honey
- Name: Martin Holloway
- Title: Creative Director
- Phone: +64 2815 96 417
- Email: martin@rimavalehoney.example.nz
- Website: www.rimavalehoney.example.nz

- Socials: ***For email Signature Only***
- Facebook: https://www.facebook.com/rimavalehoney/
- Instagram: https://www.instagram.com/rimavalehoney/

Target Market(s)

Asia/Europe Luxury, Upmarket

Contact Information for Business Card

- Logo
- Name: Martin Holloway
- Phone: +64 2815 96 417

Font styles to use
Other font styles liked:
• Champagne & Limousines (Attached)

Requirements
Must have
• Business Card & Email Signature Design.

Looking for a Sleek, Luxury, Upmarket Design.

```html
<!DOCTYPE html>
<html lang="en">
<head>
<meta charset="utf-8">
<title>Rima Vale Honey — Business Card &amp; Email Signature</title>
<link rel="stylesheet" href="https://fonts.googleapis.com/css2?family=Josefin+Sans:wght@300;400;700&family=Arimo:wght@400&family=Lato:wght@400;700&display=swap">
<style>
  :root {
    --backdrop: #444444;
    --kraft-light: #dcb88f;
    --kraft-mid: #c4955f;
    --kraft-dark: #9f6a3b;
    --ink: #333333;
    --ink-soft: #3f3f3f;
    --emboss: #a97b4f;
    --emboss-mark: #b3855a;
    --gold-top: #cfa96a;
    --gold-bottom: #f3ec9b;
    --paper: #ffffff;
    --social: #5a5a5a;
  }
  * { box-sizing: border-box; margin: 0; padding: 0; }
  html, body { width: 1200px; height: 1133px; overflow: hidden; }
  body { background: var(--backdrop); position: relative; font-family: "Arimo", sans-serif; }

  .card {
    position: absolute; width: 390px; height: 231px; top: 304px;
    background: linear-gradient(125deg, var(--kraft-light) 0%, var(--kraft-mid) 55%, var(--kraft-dark) 100%);
  }
  .card--front { left: 164px; }
  .card--back { left: 595px; }

  .brand-mark { position: absolute; border-radius: 50%; }
  .brand-name {
    position: absolute; white-space: nowrap; text-align: center;
    font-family: "Josefin Sans", sans-serif; font-weight: 300; text-transform: uppercase;
  }

  .card--front .brand-mark { width: 40px; height: 40px; left: 91px; top: 76px; background: var(--ink); }
  .card--front .brand-name { left: 0; width: 206px; top: 128px; font-size: 14px; letter-spacing: 2.5px; color: var(--ink); }
  .card__divider { position: absolute; left: 205px; top: 76px; width: 1px; height: 80px; background: #8a6440; }
  .card__details { position: absolute; left: 217px; top: 75px; color: var(--ink); }
  .card__name { font-family: "Josefin Sans", sans-serif; font-weight: 700; font-size: 14.5px; letter-spacing: .3px; line-height: 1; }
  .card__title { font-size: 10.5px; margin-top: 2px; }
  .card__contacts { list-style: none; margin-top: 13px; font-size: 9.5px; line-height: 14px; }
  .card__contacts li { display: flex; align-items: center; gap: 5px; }
  .card__contacts svg { width: 11px; height: 11px; flex: none; }

  .card--back .brand-mark { width: 64px; height: 64px; left: 163px; top: 42px; border: 1.5px solid var(--emboss-mark); }
  .card--back .brand-name { left: 0; width: 390px; top: 131px; font-size: 23px; letter-spacing: 5px; color: var(--emboss); }

  .signature { position: absolute; left: 160px; top: 630px; width: 822px; height: 247px; background: var(--paper); }
  .signature__brand {
    position: absolute; left: 0; top: 0; width: 337px; height: 247px;
    background: linear-gradient(180deg, var(--gold-top), var(--gold-bottom));
  }
  .signature__brand .brand-mark { width: 80px; height: 80px; left: 128px; top: 44px; border: 2px solid var(--ink-soft); }
  .signature__brand .brand-name { left: 0; width: 337px; top: 155px; font-size: 23px; letter-spacing: 4px; color: var(--ink-soft); font-weight: 400; }
  .signature__details { position: absolute; left: 416px; top: 20px; color: var(--ink-soft); font-family: "Lato", sans-serif; }
  .signature__name { font-size: 29px; font-weight: 700; letter-spacing: -.5px; line-height: 1.1; }
  .signature__title { font-size: 19px; line-height: 1.1; margin-top: 1px; }
  .signature__contacts { list-style: none; margin-top: 24px; font-size: 19px; line-height: 25px; }
  .signature__contacts li { display: flex; align-items: center; gap: 9px; }
  .signature__contacts svg { width: 22px; height: 22px; flex: none; }
  .signature__social { display: flex; align-items: center; margin-top: 14px; font-size: 19px; gap: 6px; }
  .signature__social-label { margin-right: 6px; }
  .social-dot { width: 27px; height: 27px; border-radius: 50%; background: var(--social); display: inline-block; }
  .signature__social-handle { margin-left: 8px; }
</style>
</head>
<body>
  <section class="card card--front" aria-label="Business card front">
    <span class="brand-mark" aria-hidden="true"></span>
    <span class="brand-name">Rima Vale Honey</span>
    <span class="card__divider"></span>
    <div class="card__details">
      <p class="card__name">MARTIN HOLLOWAY</p>
      <p class="card__title">Creative Director</p>
      <ul class="card__contacts">
        <li><svg viewBox="0 0 24 24" fill="currentColor"><path d="M6.6 10.8a15 15 0 0 0 6.6 6.6l2.2-2.2a1 1 0 0 1 1-.25 11.4 11.4 0 0 0 3.6.57 1 1 0 0 1 1 1V20a1 1 0 0 1-1 1A17 17 0 0 1 3 4a1 1 0 0 1 1-1h3.5a1 1 0 0 1 1 1c0 1.25.2 2.45.57 3.57a1 1 0 0 1-.25 1z"/></svg>+64 2815 96 417</li>
        <li><svg viewBox="0 0 24 24" fill="currentColor"><path d="M2 5h20v14H2z M2 5l10 8 10-8" stroke="#fff" stroke-width="1.2"/></svg>martin@rimavalehoney.example.nz</li>
        <li><svg viewBox="0 0 24 24" fill="none" stroke="currentColor" stroke-width="2"><circle cx="12" cy="12" r="10"/><path d="M2 12h20M12 2c3 3 3 17 0 20M12 2c-3 3-3 17 0 20"/></svg>www.rimavalehoney.example.nz</li>
      </ul>
    </div>
  </section>

  <section class="card card--back" aria-label="Business card back">
    <span class="brand-mark" aria-hidden="true"></span>
    <span class="brand-name">Rima Vale Honey</span>
  </section>

  <section class="signature" aria-label="Email signature">
    <div class="signature__brand">
      <span class="brand-mark" aria-hidden="true"></span>
      <span class="brand-name">Rima Vale Honey</span>
    </div>
    <div class="signature__details">
      <p class="signature__name">Martin Holloway</p>
      <p class="signature__title">Creative Director</p>
      <ul class="signature__contacts">
        <li><svg viewBox="0 0 24 24" fill="currentColor"><path d="M6.6 10.8a15 15 0 0 0 6.6 6.6l2.2-2.2a1 1 0 0 1 1-.25 11.4 11.4 0 0 0 3.6.57 1 1 0 0 1 1 1V20a1 1 0 0 1-1 1A17 17 0 0 1 3 4a1 1 0 0 1 1-1h3.5a1 1 0 0 1 1 1c0 1.25.2 2.45.57 3.57a1 1 0 0 1-.25 1z"/></svg>+64 2815 96 417</li>
        <li><svg viewBox="0 0 24 24" fill="currentColor"><path d="M2 5h20v14H2z M2 5l10 8 10-8" stroke="#fff" stroke-width="1.2"/></svg>martin@rimavalehoney.example.nz</li>
        <li><svg viewBox="0 0 24 24" fill="none" stroke="currentColor" stroke-width="1.8"><circle cx="12" cy="12" r="10"/><path d="M2 12h20M12 2c3 3 3 17 0 20M12 2c-3 3-3 17 0 20"/></svg>www.rimavalehoney.example.nz</li>
      </ul>
      <div class="signature__social">
        <span class="signature__social-label">Follow us on:</span>
        <a class="social-dot" href="https://social-one.example/rimavalehoney/" aria-label="Social profile one"></a>
        <a class="social-dot" href="https://social-two.example/rimavalehoney/" aria-label="Social profile two"></a>
        <span class="signature__social-handle">/ &nbsp;rimavalehoney</span>
      </div>
    </div>
  </section>
</body>
</html>
```